RESIDENTIAL CONSTRUCTION

We are a company that specializes in building custom residential homes, the design should also emphasize that quality and service is our priority.

Industry/Entity Type

Construction Company

Contact Information for Business Card

Contact Person: Marcus Lindqvist
Company Address: 273 West Alder Ave San Jose , Ca 95380
Phone Number : 408-731-2946
Email Address: Stoneridgehomes517@mailvista.net

Font styles to use
Sans Serif

Colors
ec1f27

Requirements
Must have
• CSLB # 7362015
Nice to have
• needs to have same color as logo i uploaded, we will be printing these on a clear plastic card.

```html
<!DOCTYPE html>
<html lang="en">
<head>
<meta charset="utf-8">
<title>Stoneridge Homes – Business Card</title>
<link href="https://fonts.googleapis.com/css2?family=Oswald:wght@500;600&family=Open+Sans:wght@400&display=swap" rel="stylesheet">
<style>
  :root {
    --brand-red: #ec1f27;
    --ink: #111111;
    --card-dark: #1c1c1c;
    --card-light: #f1f1f1;
    --page-bg: #2a2a2a;
    --muted: #cfcfcf;
  }
  * { box-sizing: border-box; margin: 0; padding: 0; }
  html, body { width: 1200px; height: 900px; overflow: hidden; }
  body {
    background: var(--page-bg);
    display: flex;
    flex-direction: column;
    align-items: center;
    justify-content: center;
    gap: 40px;
  }
  .card {
    width: 680px;
    height: 389px;
    position: relative;
    box-shadow: 0 10px 30px rgba(0,0,0,0.45);
  }
  .card--back {
    background: var(--card-dark);
    display: flex;
    align-items: center;
    justify-content: center;
  }
  .card--front { background: var(--card-light); }

  .wordmark {
    display: flex;
    align-items: center;
    gap: 12px;
  }
  .wordmark__square {
    width: 22px;
    height: 22px;
    background: var(--brand-red);
  }
  .wordmark__name {
    font-family: "Oswald", sans-serif;
    font-weight: 600;
    text-transform: uppercase;
    letter-spacing: 1px;
    color: var(--brand-red);
  }
  .card--back .wordmark__name { font-size: 50px; }
  .card--front .wordmark {
    position: absolute;
    top: 120px;
    right: 52px;
  }
  .card--front .wordmark__name { font-size: 38px; }
  .card--front .wordmark__square { width: 18px; height: 18px; }

  .identity {
    position: absolute;
    top: 42px;
    left: 52px;
  }
  .identity__name {
    font-family: "Oswald", sans-serif;
    font-weight: 600;
    font-size: 27px;
    text-transform: uppercase;
    color: var(--ink);
    line-height: 1.1;
  }
  .identity__title {
    font-family: "Oswald", sans-serif;
    font-weight: 500;
    font-size: 15px;
    text-transform: uppercase;
    color: var(--brand-red);
    margin-top: 2px;
  }
  .identity__rule {
    width: 72px;
    height: 2px;
    background: var(--brand-red);
    margin-top: 8px;
  }

  .contact {
    position: absolute;
    left: 52px;
    bottom: 50px;
    list-style: none;
    font-family: "Open Sans", sans-serif;
    font-size: 17px;
    color: var(--ink);
  }
  .contact__item {
    display: flex;
    align-items: center;
    gap: 12px;
    line-height: 1.55;
  }
  .contact__icon { width: 14px; height: 14px; flex: none; }
</style>
</head>
<body>
  <section class="card card--back" aria-label="Card back">
    <div class="wordmark">
      <span class="wordmark__square"></span>
      <span class="wordmark__name">Stoneridge Homes</span>
    </div>
  </section>

  <section class="card card--front" aria-label="Card front">
    <div class="identity">
      <h1 class="identity__name">Marcus Lindqvist</h1>
      <p class="identity__title">Job Title | CSLB # 7362015</p>
      <div class="identity__rule"></div>
    </div>

    <div class="wordmark">
      <span class="wordmark__square"></span>
      <span class="wordmark__name">Stoneridge Homes</span>
    </div>

    <ul class="contact">
      <li class="contact__item">
        <svg class="contact__icon" viewBox="0 0 24 24" aria-hidden="true"><path fill="#ec1f27" d="M6.6 10.8a15.1 15.1 0 0 0 6.6 6.6l2.2-2.2a1 1 0 0 1 1-.25 11.4 11.4 0 0 0 3.6.57 1 1 0 0 1 1 1V20a1 1 0 0 1-1 1A17 17 0 0 1 3 4a1 1 0 0 1 1-1h3.5a1 1 0 0 1 1 1c0 1.25.2 2.45.57 3.57a1 1 0 0 1-.25 1z"/></svg>
        <span>408-731-2946</span>
      </li>
      <li class="contact__item">
        <svg class="contact__icon" viewBox="0 0 24 24" aria-hidden="true"><path fill="#ec1f27" d="M2 5h20v14H2z"/><path fill="none" stroke="#f1f1f1" stroke-width="2" d="M2 5l10 8 10-8"/></svg>
        <span>Stoneridgehomes517@mailvista.net</span>
      </li>
      <li class="contact__item">
        <svg class="contact__icon" viewBox="0 0 24 24" aria-hidden="true"><path fill="#ec1f27" d="M12 2a7 7 0 0 0-7 7c0 5.2 7 13 7 13s7-7.8 7-13a7 7 0 0 0-7-7zm0 9.5A2.5 2.5 0 1 1 12 6.5a2.5 2.5 0 0 1 0 5z"/></svg>
        <span>273 West Alder Ave San Jose , Ca 95380</span>
      </li>
    </ul>
  </section>
</body>
</html>
```